Lifestyle Coaching comp needs wordpress design. We focus on strong mindsets, fitness and nutrition

BrenVigor Lifestyle Coaching needs a wordpress site. Our tagline for now (may change) is Mindset Mastery.Fitness Badassery. Sustainable Nutrition
Our logo is below. Would like to see some complimentary colors to liven it up. Clients need to come to site and get immediate professional, but fun feel. They need to have the impression that we are the last destination in their journey to wellness. Blogging, workout videos, pictures

Target Market(s)

Mostly women ages 20+

Industry/Entity Type

Nutrition

Colors
33a6d7
86cae7
ceeaf6
cfdeed
5c5c5c
cbcbcb
474747

Requirements
Must have
• A strong, badass feel :) While not being intimidating
Nice to have
• Fun fonts. Love the font in my logo
Should not have
• Pics, logos of flowers, heads, fruit.

```html
<!DOCTYPE html>
<html lang="en">
<head>
<meta charset="utf-8">
<title>BrenVigor Lifestyle Coaching</title>
<link rel="stylesheet" href="https://fonts.googleapis.com/css2?family=Open+Sans:wght@400;600&family=Varela+Round&family=Tienne&family=Arimo&display=swap">
<style>
:root{
  --blue:#33a6d7;
  --blue-light:#86cae7;
  --blue-pale:#ceeaf6;
  --ink:#222;
  --grey:#5c5c5c;
  --grey-soft:#8a8a8a;
  --line:#cbcbcb;
  --dark:#2b2b2b;
  --white:#fff;
}
*{margin:0;padding:0;box-sizing:border-box}
html,body{width:678px;height:1200px;overflow:hidden;background:var(--white)}
body{position:relative;font-family:"Open Sans",sans-serif;color:var(--ink)}
.abs{position:absolute}

/* header */
.site-header{left:0;top:0;width:678px;height:60px;text-align:center}
.brand{position:absolute;left:0;right:0;top:12px;display:flex;flex-direction:column;align-items:center;gap:2px}
.brand-row{display:flex;align-items:center;gap:6px}
.brand-dot{width:12px;height:12px;border-radius:50%;background:var(--blue)}
.brand-name{font-family:"Open Sans",sans-serif;font-weight:600;font-size:15px;letter-spacing:2px;color:var(--blue)}
.brand-sub{font-size:5px;letter-spacing:2px;color:var(--grey);text-transform:uppercase}

.main-nav{left:0;top:60px;width:678px;height:30px;background:var(--blue);display:flex;padding-left:50px}
.main-nav a{display:flex;align-items:center;justify-content:center;height:30px;color:var(--white);font-size:8px;text-decoration:none;border-right:1px solid rgba(255,255,255,.18)}
.main-nav a.active{background:var(--blue-light)}
.nav-burger{width:40px;border-left:1px solid rgba(255,255,255,.18)}

/* hero */
.hero{left:0;top:90px;width:678px;height:316px;background:linear-gradient(100deg,#e0669a 0%,#d8a79c 28%,#e9ecef 50%,#c9d8de 72%,#2f8fb6 100%)}
.hero-tagline{left:0;right:0;top:232px;text-align:center;font-family:"Tienne",serif;font-size:21px;color:#111}
.hero-arrow{top:232px;font-size:24px;color:var(--blue-light);font-family:"Open Sans",sans-serif}

/* section headings */
.heading{font-family:"Open Sans",sans-serif;font-weight:600;font-size:16px;color:var(--ink)}
.heading span{color:var(--blue)}

/* programs */
.program{width:180px;text-align:center}
.program-photo{width:106px;height:106px;margin:0 auto;border-radius:50%;border:4px solid var(--blue);box-shadow:0 2px 3px rgba(0,0,0,.25)}
.program-title{margin-top:13px;font-family:"Varela Round",sans-serif;font-size:12.5px;color:var(--blue)}
.program-text{margin-top:6px;font-family:"Arimo",sans-serif;font-size:6.5px;line-height:13px;color:var(--grey-soft)}
.program-more{margin-top:5px;font-size:10px;color:var(--ink)}

/* videos */
.videos{left:0;top:676px;width:678px;height:232px;background:linear-gradient(90deg,#7d8a83,#6f7d6a 50%,#566b4a)}
.videos .heading{color:var(--white)}
.video-frame{top:738px;width:280px;height:131px;border:3px solid var(--white)}
.play{left:50%;top:50%;width:20px;height:20px;margin:-10px 0 0 -10px;border-radius:50%;background:rgba(40,40,40,.75)}
.play:after{content:"";position:absolute;left:8px;top:6px;border-left:6px solid var(--white);border-top:4px solid transparent;border-bottom:4px solid transparent}
.slide-btn{top:793px;width:18px;height:20px;background:#222;color:var(--white);font-size:8px;display:flex;align-items:center;justify-content:center}

/* lower columns */
.about-photo{left:50px;top:963px;width:164px;height:73px;background:linear-gradient(180deg,#d6e3ee,#8cb4d3 60%,#3b79c4)}
.about-text{left:50px;width:165px;font-family:"Arimo",sans-serif;font-size:6.5px;line-height:11px;color:var(--grey);text-align:justify}
.post{left:243px;width:200px;height:50px}
.post-thumb{width:51px;height:49px}
.post-body{position:absolute;left:61px;top:0;width:140px}
.post-title{font-size:7.5px;color:var(--ink);letter-spacing:.2px}
.post-excerpt{margin-top:4px;font-family:"Arimo",sans-serif;font-size:5.5px;line-height:11px;color:var(--grey)}
.post-meta{font-size:4.8px;color:var(--blue)}
.tile{width:51px;height:73px;border:2px solid #eee;box-shadow:0 0 1px var(--line)}

/* footer */
.site-footer{left:0;top:1150px;width:678px;height:50px;background:var(--dark)}
.copyright{left:51px;top:20px;font-size:6.5px;color:var(--white)}
.social{top:16px;width:19px;height:19px;border-radius:3px}
</style>
</head>
<body>

<header class="site-header abs">
  <div class="brand">
    <div class="brand-row"><span class="brand-dot"></span><span class="brand-name">BRENVIGOR</span></div>
    <div class="brand-sub">Lifestyle Coaching</div>
  </div>
</header>

<nav class="main-nav abs">
  <a class="nav-burger" href="#" aria-label="Menu">
    <svg width="11" height="9" viewBox="0 0 11 9"><rect width="11" height="1.6" fill="#fff"/><rect y="3.7" width="11" height="1.6" fill="#fff"/><rect y="7.4" width="11" height="1.6" fill="#fff"/></svg>
  </a>
  <a class="active" href="#" style="width:56px">Home</a>
  <a href="#" style="width:72px">About Us</a>
  <a href="#" style="width:72px">Programs</a>
  <a href="#" style="width:96px">Workout videos</a>
  <a href="#" style="width:60px">Gallery</a>
  <a href="#" style="width:53px">Blog</a>
  <a href="#" style="width:65px">Contact</a>
  <a href="#" style="width:88px;border-right:0" aria-label="Search">
    <svg width="10" height="10" viewBox="0 0 10 10"><circle cx="4" cy="4" r="3" fill="none" stroke="#fff" stroke-width="1.5"/><line x1="6.2" y1="6.2" x2="9" y2="9" stroke="#fff" stroke-width="1.6"/></svg>
  </a>
</nav>

<section class="hero abs" role="img" aria-label="Smiling women riding exercise bikes in a spin class"></section>
<span class="hero-arrow abs" style="left:30px">&#x2039;</span>
<p class="hero-tagline abs">Mindset Mastery.Fitness Badassery. Sustainable Nutrition</p>
<span class="hero-arrow abs" style="left:637px">&#x203A;</span>

<h2 class="heading abs" style="left:0;right:0;top:429px;text-align:center">Our <span>Programs</span></h2>

<article class="program abs" style="left:55px;top:462px">
  <div class="program-photo" role="img" aria-label="Woman meditating outdoors in autumn" style="background:radial-gradient(circle,#b88a5e,#a4521f)"></div>
  <h3 class="program-title">Mindset Mastery</h3>
  <p class="program-text">Arenean nonummy hendrerit mau phaselntes nascetur ridic ulusm dui fusce feu. Cras vitae neque turpis, in luctus risus. Donec et...</p>
  <p class="program-more">Know More &nbsp;&raquo;</p>
</article>
<article class="program abs" style="left:248px;top:462px">
  <div class="program-photo" role="img" aria-label="Woman resting beside fruit and a dumbbell" style="background:radial-gradient(circle,#f4ece2,#e7d5c2)"></div>
  <h3 class="program-title">Fitness and Nutrition</h3>
  <p class="program-text">Arenean nonummy hendrerit mau phaselntes nascetur ridic ulusm dui fusce feu. Cras vitae neque turpis, in luctus risus. Donec et...</p>
  <p class="program-more">Know More &nbsp;&raquo;</p>
</article>
<article class="program abs" style="left:441px;top:462px">
  <div class="program-photo" role="img" aria-label="Couple lifting dumbbells in a gym" style="background:radial-gradient(circle,#b7b7b7,#4a4a4a)"></div>
  <h3 class="program-title">Exercises</h3>
  <p class="program-text">Arenean nonummy hendrerit mau phaselntes nascetur ridic ulusm dui fusce feu. Cras vitae neque turpis, in luctus risus. Donec et...</p>
  <p class="program-more">Know More &nbsp;&raquo;</p>
</article>

<section class="videos abs" role="img" aria-label="Blurred outdoor background of a woman exercising on grass"></section>
<h2 class="heading abs" style="left:0;right:0;top:701px;text-align:center;color:#fff">Workout <span>Videos</span></h2>
<div class="video-frame abs" style="left:50px;background:linear-gradient(90deg,#d9e6ee,#8d74b8 30%,#f08a3b 55%,#98c25a 75%,#e9edf0)" role="img" aria-label="Women working out on exercise bikes">
  <span class="play abs"></span>
</div>
<div class="video-frame abs" style="left:349px;background:linear-gradient(180deg,#9ec36b,#5f8d3d 55%,#3e6a2a)" role="img" aria-label="Two older women meditating in a park">
  <span class="play abs"></span>
</div>
<span class="slide-btn abs" style="left:53px">&#9664;</span>
<span class="slide-btn abs" style="left:608px">&#9654;</span>

<h2 class="heading abs" style="left:50px;top:929px">About <span>Us</span></h2>
<div class="about-photo abs" role="img" aria-label="Group fitness class with dumbbells and exercise balls"></div>
<p class="about-text abs" style="top:1042px">Fusce euismod consequat ante. Lorem sit amet, consectetuer adipiscing elit. Pellentesque sed dolor.</p>
<p class="about-text abs" style="top:1075px">Praesent justo dolor, lobortis quis, lobortis dignissim, pulvinar ac, consequat ante. Lorem ipsum dolor sit amet, consectetuer adipiscing elit. Pellentesque sed dolor. Aliquam congue fermentum nisl.</p>

<h2 class="heading abs" style="left:242px;top:929px">Latest <span>Blog</span></h2>
<article class="post abs" style="top:963px">
  <div class="post-thumb" role="img" aria-label="People training with exercise balls" style="background:linear-gradient(180deg,#6ea0d6,#2f66b3)"></div>
  <div class="post-body">
    <h4 class="post-title">LABORE ET DOLORE MAGNAM</h4>
    <p class="post-excerpt">Neque porro quisquam est, qui dolorem ipsum quia dolor sit amet, consectetur, adipisci velit.</p>
    <p class="post-meta">7 Jan 215 &nbsp;&nbsp;&nbsp;&nbsp; (23) &nbsp; 34 comments</p>
  </div>
</article>
<article class="post abs" style="top:1017px">
  <div class="post-thumb" role="img" aria-label="Woman drinking water after a workout" style="background:linear-gradient(180deg,#f6cf58,#e88a6a)"></div>
  <div class="post-body">
    <h4 class="post-title">LABORE ET DOLORE MAGNAM</h4>
    <p class="post-excerpt">Neque porro quisquam est, qui dolorem ipsum quia dolor sit amet, consectetur, adipisci velit.</p>
    <p class="post-meta">7 Jan 215 &nbsp;&nbsp;&nbsp;&nbsp; (23) &nbsp; 34 comments</p>
  </div>
</article>
<article class="post abs" style="top:1071px">
  <div class="post-thumb" role="img" aria-label="Woman with a healthy meal" style="background:linear-gradient(180deg,#f3f1ec,#8fbf5a)"></div>
  <div class="post-body">
    <h4 class="post-title">LABORE ET DOLORE MAGNAM</h4>
    <p class="post-excerpt">Neque porro quisquam est, qui dolorem ipsum quia dolor sit amet, consectetur, adipisci velit.</p>
    <p class="post-meta">7 Jan 215 &nbsp;&nbsp;&nbsp;&nbsp; (23) &nbsp; 34 comments</p>
  </div>
</article>

<h2 class="heading abs" style="left:458px;top:929px">Gallery</h2>
<div class="tile abs" style="left:462px;top:965px;background:linear-gradient(180deg,#b7d08a,#3fa9b5)" role="img" aria-label="Woman running outdoors"></div>
<div class="tile abs" style="left:519px;top:965px;background:linear-gradient(180deg,#3a8fd0,#e05a9a)" role="img" aria-label="Women at a fitness class"></div>
<div class="tile abs" style="left:577px;top:965px;background:linear-gradient(180deg,#d8e4ea,#4b86c6)" role="img" aria-label="Woman stretching with an exercise ball"></div>
<div class="tile abs" style="left:462px;top:1046px;background:linear-gradient(180deg,#8fb27a,#b85a4c)" role="img" aria-label="Two women jogging on a track"></div>
<div class="tile abs" style="left:519px;top:1046px;background:linear-gradient(180deg,#5a5a5a,#1e1e1e)" role="img" aria-label="Woman doing a plank"></div>
<div class="tile abs" style="left:577px;top:1046px;background:linear-gradient(180deg,#a6cf6b,#d64f94)" role="img" aria-label="Woman doing yoga on grass"></div>

<footer class="site-footer abs">
  <p class="copyright abs">BrenVigor&copy; 2015 All Rights Reserved Privacy Policy</p>
  <span class="social abs" style="left:532px;background:#3b5aa8" aria-label="Social link"></span>
  <span class="social abs" style="left:558px;background:#2f9fe0" aria-label="Social link"></span>
  <span class="social abs" style="left:584px;background:#1e73b4" aria-label="Social link"></span>
  <span class="social abs" style="left:610px;background:#ee8a1e" aria-label="Feed link"></span>
</footer>

</body>
</html>
```